High-end construction company needs a business card design

We need a modern looking business card that draws people in, is memorable and looks so good people will want to sick it on their fridges.
On the first side what is needed are:
Logo
My name - Tomasz Brelwik
Title - Managing Director
Website - www.varkelt.co.uk
Email - tomasz@varkelt.co.uk
Telephone - 020 5194 6281
Mobile - 07845139072
On the back side was is needed is a list of all the services we provide:
-Kitchen Renovations
-Bathroom Renovations
-House Renovations
-Garage Conversions
-Extensions
-Loft Conversions
-Conservatories
-Carpentry
-Tiling
-Electrical
-Plumbing & Heating
-Bricklaying
-Landscaping
-Decorating
-Plastering
We would like the colours to be the same shades as on the logo with grey or black for the words.
Target Market(s)
Anyone who needs building work done
Contact Information for Business Card
This business card is for a construction company which strives to deliver excellent service and quality.
The look and feel of the card should represent this.
Requirements
Must have
- On the first side what is needed are:
Logo
My name - Tomasz Brelwik
Title - Managing Director
Website - www.varkelt.co.uk
Email - tomasz@varkelt.co.uk
Telephone - 020 5194 6281
Mobile - 07845139072
Nice to have
- Cool looking features

```html
<!DOCTYPE html>
<html lang="en">
<head>
<meta charset="utf-8">
<title>Varkelt Construction – Business Card</title>
<link rel="stylesheet" href="https://fonts.googleapis.com/css2?family=Montserrat:wght@500;600;700&family=Exo+2:wght@300;400&display=swap">
<style>
  :root {
    --bg: #d9d9d9;
    --card-white: #ffffff;
    --green-light: #6cc04a;
    --green-dark: #3a7d2c;
    --green-back-a: #347a2d;
    --green-back-b: #66a45d;
    --text-grey: #555555;
    --white: #ffffff;
  }
  * { box-sizing: border-box; margin: 0; padding: 0; }
  html, body { width: 1200px; height: 1200px; overflow: hidden; background: var(--bg); }
  .canvas { position: relative; width: 1200px; height: 1200px; }

  .card {
    position: absolute;
    left: 257px;
    width: 686px;
    height: 392px;
    box-shadow: 0 18px 30px rgba(0,0,0,0.25);
  }
  .card--front { top: 165px; background: var(--card-white); }
  .card--back {
    top: 653px;
    background: linear-gradient(35deg, var(--green-back-a), var(--green-back-b));
    color: var(--white);
  }

  /* Front: brand name */
  .brand {
    position: absolute; right: 64px; top: 100px;
    display: flex; align-items: center; gap: 12px;
    font-family: "Montserrat", sans-serif; font-weight: 700;
    color: var(--green-light);
  }
  .brand__mark { width: 44px; height: 44px; background: var(--green-light); flex: none; }
  .brand__text { display: flex; flex-direction: column; align-items: stretch; }
  .brand__name { font-size: 40px; line-height: 42px; letter-spacing: 1px; }
  .brand__sub { font-size: 11.5px; letter-spacing: 2.6px; text-align: center; margin-top: 4px; }

  .person { position: absolute; left: 47px; top: 235px; font-family: "Montserrat", sans-serif; }
  .person__name { font-size: 24px; font-weight: 700; color: var(--green-light); letter-spacing: 0.5px; line-height: 28px; }
  .person__title { font-size: 14.5px; font-weight: 600; color: var(--green-dark); margin-top: 1px; }

  .divider { position: absolute; left: 47px; top: 292px; width: 575px; height: 2px; background: var(--green-dark); }

  .contacts {
    position: absolute; top: 303px; list-style: none;
    font-family: "Montserrat", sans-serif; font-weight: 500; font-size: 17px; color: var(--text-grey);
  }
  .contacts li { display: flex; align-items: center; gap: 10px; height: 21px; }
  .contacts--left { left: 48px; }
  .contacts--right { right: 64px; }
  .contacts svg { width: 13px; height: 13px; fill: var(--green-dark); flex: none; }

  /* Back: brand name as large centrepiece */
  .back-brand {
    position: absolute; left: 0; right: 0; top: 100px;
    display: flex; justify-content: center; align-items: center; gap: 18px;
    font-family: "Montserrat", sans-serif; font-weight: 700;
    font-size: 64px; line-height: 70px; letter-spacing: 2px; color: var(--white);
  }
  .back-brand__mark { width: 62px; height: 62px; background: var(--white); flex: none; }
  .back-rule { position: absolute; left: 148px; width: 372px; top: 209px; height: 2px; background: var(--white); }

  .services {
    position: absolute; left: 0; right: 0; top: 232px;
    text-align: center;
    font-family: "Exo 2", sans-serif; font-weight: 300;
    font-size: 16px; line-height: 21.5px; letter-spacing: 0.2px;
  }
  .services .tick { display: inline-block; width: 12px; height: 12px; vertical-align: -1px; margin: 0 3px; }
  .socials { position: absolute; left: 0; right: 0; top: 347px; display: flex; justify-content: center; gap: 5px; }
  .socials span { width: 21px; height: 21px; border: 1.6px solid var(--white); border-radius: 6px; }
</style>
</head>
<body>
<div class="canvas">

  <section class="card card--front">
    <div class="brand">
      <span class="brand__mark"></span>
      <div class="brand__text">
        <span class="brand__name">VARKELT</span>
        <span class="brand__sub">CONSTRUCTION LTD</span>
      </div>
    </div>

    <div class="person">
      <div class="person__name">TOMASZ BRELWIK</div>
      <div class="person__title">Managing Director</div>
    </div>

    <div class="divider"></div>

    <ul class="contacts contacts--left">
      <li><svg viewBox="0 0 16 16"><path d="M3.5 1l3 3-1.8 2a9 9 0 0 0 5.3 5.3l2-1.8 3 3-2 2C7 14 2 9 1.5 3z"/></svg>020 5194 6281</li>
      <li><svg viewBox="0 0 16 16"><path d="M4 0h8a1 1 0 0 1 1 1v14a1 1 0 0 1-1 1H4a1 1 0 0 1-1-1V1a1 1 0 0 1 1-1zm1 2v10h6V2z"/></svg>07845139072</li>
    </ul>

    <ul class="contacts contacts--right">
      <li><svg viewBox="0 0 16 16"><path d="M1 3h14v10H1zm1.5 1.5v.3L8 9l5.5-4.2v-.3z"/></svg>tomasz@varkelt.co.uk</li>
      <li><svg viewBox="0 0 16 16"><circle cx="8" cy="8" r="7"/></svg>www.varkelt.co.uk</li>
    </ul>
  </section>

  <section class="card card--back">
    <div class="back-brand">
      <span class="back-brand__mark"></span>
      <span>VARKELT</span>
    </div>
    <div class="back-rule"></div>

    <p class="services">
      Kitchen Renovations<svg class="tick" viewBox="0 0 12 12"><rect x="0.7" y="0.7" width="10.6" height="10.6" fill="none" stroke="#fff" stroke-width="1.4"/><path d="M3 6l2 2 4-4.5" fill="none" stroke="#fff" stroke-width="1.6"/></svg>Bathroom Renovations<svg class="tick" viewBox="0 0 12 12"><rect x="0.7" y="0.7" width="10.6" height="10.6" fill="none" stroke="#fff" stroke-width="1.4"/><path d="M3 6l2 2 4-4.5" fill="none" stroke="#fff" stroke-width="1.6"/></svg>House Renovations<br>
      Garage Conversions<svg class="tick" viewBox="0 0 12 12"><rect x="0.7" y="0.7" width="10.6" height="10.6" fill="none" stroke="#fff" stroke-width="1.4"/><path d="M3 6l2 2 4-4.5" fill="none" stroke="#fff" stroke-width="1.6"/></svg>Extensions<svg class="tick" viewBox="0 0 12 12"><rect x="0.7" y="0.7" width="10.6" height="10.6" fill="none" stroke="#fff" stroke-width="1.4"/><path d="M3 6l2 2 4-4.5" fill="none" stroke="#fff" stroke-width="1.6"/></svg>Loft Conversions<svg class="tick" viewBox="0 0 12 12"><rect x="0.7" y="0.7" width="10.6" height="10.6" fill="none" stroke="#fff" stroke-width="1.4"/><path d="M3 6l2 2 4-4.5" fill="none" stroke="#fff" stroke-width="1.6"/></svg>Conservatories<br>
      Carpentry<svg class="tick" viewBox="0 0 12 12"><rect x="0.7" y="0.7" width="10.6" height="10.6" fill="none" stroke="#fff" stroke-width="1.4"/><path d="M3 6l2 2 4-4.5" fill="none" stroke="#fff" stroke-width="1.6"/></svg>Tiling<svg class="tick" viewBox="0 0 12 12"><rect x="0.7" y="0.7" width="10.6" height="10.6" fill="none" stroke="#fff" stroke-width="1.4"/><path d="M3 6l2 2 4-4.5" fill="none" stroke="#fff" stroke-width="1.6"/></svg>Electrical<svg class="tick" viewBox="0 0 12 12"><rect x="0.7" y="0.7" width="10.6" height="10.6" fill="none" stroke="#fff" stroke-width="1.4"/><path d="M3 6l2 2 4-4.5" fill="none" stroke="#fff" stroke-width="1.6"/></svg>Plumbing &amp; Heating<svg class="tick" viewBox="0 0 12 12"><rect x="0.7" y="0.7" width="10.6" height="10.6" fill="none" stroke="#fff" stroke-width="1.4"/><path d="M3 6l2 2 4-4.5" fill="none" stroke="#fff" stroke-width="1.6"/></svg>Bricklaying<br>
      Landscaping<svg class="tick" viewBox="0 0 12 12"><rect x="0.7" y="0.7" width="10.6" height="10.6" fill="none" stroke="#fff" stroke-width="1.4"/><path d="M3 6l2 2 4-4.5" fill="none" stroke="#fff" stroke-width="1.6"/></svg>Decorating<svg class="tick" viewBox="0 0 12 12"><rect x="0.7" y="0.7" width="10.6" height="10.6" fill="none" stroke="#fff" stroke-width="1.4"/><path d="M3 6l2 2 4-4.5" fill="none" stroke="#fff" stroke-width="1.6"/></svg>Plastering
    </p>

    <div class="socials" aria-label="Social media links">
      <span></span><span></span><span></span>
    </div>
  </section>

</div>
</body>
</html>
```